I need a flyer made , the flyer can be one page or two pages or three pages . I will be posting this on Instagram and social media platforms. I am a luxury home builder , I am looking to hire a construction project manager . Below are some examples and ideas what can be on the flyer

We’re looking for a construction project manager who’s passionate about building luxury homes at the highest standards
We’re hiring construction project manager
* Experience 5+ years in residential project management with a strong portfolio of completed homes.
* location : Bergen County NJ
* excellent leadership skills, leads teams with confidence and clarity
* communicates seamlessly with architects , engineers, designers and clients
*knows how to manage budgets and timelines without compromising quality
*solves problems with a positive solution first mindset
* pays attention to every detail because in luxury the small things are the big things

Apply now , link in bio or DM to connect.

My logo is attached, my web site www.velstridebuilders.com
My style is modern but still warm and inviting. I like a clean classy look .

Please don’t add any images of chairs or people to the flyer , I do not want people on my flyer. Do not add standard images of offices and houses , we are luxury builders , we build homes over 2 million dollars. Keep a classy , simple modern look . High end .

You can add a white hard hat with my logo on it for a image , this is a suggestion does not have to be on my flyer ,

```html
<!DOCTYPE html>
<html lang="en">
<head>
<meta charset="utf-8">
<title>Hiring – Construction Project Manager</title>
<link rel="stylesheet" href="https://fonts.googleapis.com/css2?family=Poppins:wght@400;500;600;700;800&family=Roboto+Condensed:wght@700&family=Bebas+Neue&display=swap">
<style>
  :root{
    --backdrop:#3a3a3a;
    --paper:#e9e9e9;
    --ink:#0c0c0c;
    --tan:#c8b088;
    --tan-deep:#b89c6e;
    --white:#ffffff;
    --photo-light:#f2f2f2;
    --photo-mid:#d4d4d4;
  }
  *{margin:0;padding:0;box-sizing:border-box}
  html,body{width:1200px;height:1194px;overflow:hidden;background:var(--backdrop)}
  .flyer{
    position:absolute;left:114px;top:111px;width:972px;height:972px;
    background:linear-gradient(180deg,#e4e4e4 0%,#ececec 55%,#e6e6e6 100%);
    overflow:hidden;font-family:'Poppins',sans-serif;color:var(--ink);
  }
  .site-backdrop{
    position:absolute;inset:0;
    background:linear-gradient(170deg,#dcdcdc 0%,#e8e8e8 45%,#ececec 100%);
  }
  .hero-photo{
    position:absolute;left:610px;top:209px;width:350px;height:664px;
    background:radial-gradient(ellipse at 55% 40%,var(--photo-light) 0%,#e2e2e2 55%,rgba(230,230,230,0) 80%);
  }
  .headline{position:absolute;left:58px;top:48px;line-height:.86;font-weight:800;letter-spacing:-2px}
  .headline .line-1{display:block;font-size:100px;font-weight:600}
  .headline .line-2{display:block;font-size:140px;letter-spacing:-4px}
  .role-tag{
    position:absolute;left:108px;top:264px;width:482px;height:58px;
    background:var(--tan);transform:rotate(-5deg);
    box-shadow:3px 4px 6px rgba(0,0,0,.18);
    font-family:'Roboto Condensed',sans-serif;font-weight:700;font-size:33px;
    display:flex;align-items:center;justify-content:center;letter-spacing:-.2px;
  }
  .tag-icon{position:absolute;left:84px;top:244px;width:46px;height:46px;transform:rotate(-10deg)}
  .tagline{position:absolute;left:60px;top:372px;font-size:25px;font-weight:500;letter-spacing:6.3px}
  .location{position:absolute;left:59px;top:414px;display:flex;height:50px}
  .location .label{width:186px;background:var(--ink);color:var(--white);font-size:26px;font-weight:500;display:flex;align-items:center;justify-content:center}
  .location .value{width:345px;background:var(--tan);font-size:30px;font-weight:700;display:flex;align-items:center;padding-left:22px}
  .qualities{position:absolute;left:62px;top:505px;list-style:none;width:470px}
  .qualities li{position:relative;padding-left:30px;font-size:18.5px;line-height:22.5px;font-weight:500;margin-bottom:15px}
  .qualities li strong{font-weight:700}
  .qualities .tick{position:absolute;left:0;top:4px;width:16px;height:16px}
  .brand{position:absolute;left:664px;top:60px;width:270px;text-align:center;font-family:'Poppins',sans-serif;font-weight:400;color:var(--ink)}
  .brand .name{display:block;font-size:36px;letter-spacing:2px;line-height:1}
  .brand .sub{display:block;font-size:13px;letter-spacing:3px;margin-top:10px}
  .badge{position:absolute;left:632px;top:600px;width:260px;height:260px}
  .badge-text{position:absolute;left:632px;top:648px;width:260px;text-align:center}
  .badge-text .kicker{display:block;font-family:'Bebas Neue',sans-serif;font-size:40px;line-height:.95}
  .badge-text .years{display:block;font-family:'Bebas Neue',sans-serif;font-size:44px;line-height:.95}
  .badge-text .years small{font-size:30px}
  .badge-text .detail{display:block;font-size:14.5px;font-weight:500;line-height:19.5px;margin-top:4px}
  .apply{position:absolute;left:64px;top:835px;width:232px;height:64px;border:2px solid var(--ink);background:var(--tan);box-shadow:2px 3px 0 rgba(0,0,0,.35);display:flex;align-items:center;justify-content:flex-end;padding-right:16px;font-family:'Bebas Neue',sans-serif;font-size:46px;line-height:1}
  .apply-icon{position:absolute;left:60px;top:830px;width:62px;height:62px}
  .connect{position:absolute;left:311px;top:838px;font-size:21px;font-weight:600}
  .handle{position:absolute;left:314px;top:870px;display:flex;align-items:center;gap:12px;font-size:22px;font-weight:600}
  .handle .dot{width:24px;height:24px;border-radius:50%;background:var(--tan)}
  .website{position:absolute;left:645px;top:883px;font-size:15px;letter-spacing:.6px}
  .website strong{font-weight:600}
</style>
</head>
<body>
<main class="flyer">
  <div class="site-backdrop" role="img" aria-label="Faded photograph of a timber-framed house under construction"></div>
  <div class="hero-photo" role="img" aria-label="Photograph of a project manager in a white hard hat holding a clipboard"></div>

  <div class="brand"><span class="name">VELSTRIDE</span><span class="sub">builders</span></div>

  <h1 class="headline"><span class="line-1">WE’RE</span><span class="line-2">HIRING!</span></h1>

  <svg class="tag-icon" viewBox="0 0 48 48" fill="none" stroke="#0c0c0c" stroke-width="3" stroke-linejoin="round" stroke-linecap="round">
    <path d="M8 22 L30 10 L30 38 L8 28 Z" fill="#fff"/>
    <rect x="3" y="21" width="6" height="8" fill="#fff"/>
    <path d="M12 29 L16 42 L22 41 L19 31"/>
    <path d="M36 18 L42 14 M37 24 L44 24 M36 30 L42 34"/>
  </svg>
  <div class="role-tag">Construction Project Manager</div>

  <p class="tagline">Build Luxury. Lead Excellence.</p>

  <div class="location"><span class="label">LOCATION</span><span class="value">Bergen County, NJ</span></div>

  <ul class="qualities">
    <li><svg class="tick" viewBox="0 0 16 16"><circle cx="8" cy="8" r="8" fill="var(--tan)"/><path d="M4.5 8.3 L7 10.6 L11.5 5.6" stroke="#fff" stroke-width="2" fill="none"/></svg><strong>Excellent leadership skills</strong>, leads teams with confidence and clarity</li>
    <li><svg class="tick" viewBox="0 0 16 16"><circle cx="8" cy="8" r="8" fill="var(--tan)"/><path d="M4.5 8.3 L7 10.6 L11.5 5.6" stroke="#fff" stroke-width="2" fill="none"/></svg><strong>Communicates seamlessly</strong> with architects engineers, designers and clients</li>
    <li><svg class="tick" viewBox="0 0 16 16"><circle cx="8" cy="8" r="8" fill="var(--tan)"/><path d="M4.5 8.3 L7 10.6 L11.5 5.6" stroke="#fff" stroke-width="2" fill="none"/></svg><strong>Knows how to manage</strong> budgets and timelines without compromising quality</li>
    <li><svg class="tick" viewBox="0 0 16 16"><circle cx="8" cy="8" r="8" fill="var(--tan)"/><path d="M4.5 8.3 L7 10.6 L11.5 5.6" stroke="#fff" stroke-width="2" fill="none"/></svg><strong>Solves problems with</strong> a positive solution first mindset</li>
    <li><svg class="tick" viewBox="0 0 16 16"><circle cx="8" cy="8" r="8" fill="var(--tan)"/><path d="M4.5 8.3 L7 10.6 L11.5 5.6" stroke="#fff" stroke-width="2" fill="none"/></svg><strong>Pays attention to every detail</strong> because in luxury the small things are the big things</li>
  </ul>

  <svg class="badge" viewBox="0 0 260 260">
    <g fill="var(--tan)" transform="translate(130 130)">
      <rect x="-88" y="-88" width="176" height="176"/>
      <rect x="-88" y="-88" width="176" height="176" transform="rotate(15)"/>
      <rect x="-88" y="-88" width="176" height="176" transform="rotate(30)"/>
      <rect x="-88" y="-88" width="176" height="176" transform="rotate(45)"/>
      <rect x="-88" y="-88" width="176" height="176" transform="rotate(60)"/>
      <rect x="-88" y="-88" width="176" height="176" transform="rotate(75)"/>
    </g>
  </svg>
  <div class="badge-text">
    <span class="kicker">EXPERIENCE</span>
    <span class="years">5<small>+</small> YEARS</span>
    <span class="detail">in residential project<br>management with a<br>strong portfolio of<br>completed homes.</span>
  </div>

  <div class="apply">APPLY NOW</div>
  <svg class="apply-icon" viewBox="0 0 48 48" fill="none" stroke="#0c0c0c" stroke-width="2.6" stroke-linejoin="round" stroke-linecap="round">
    <g transform="rotate(-30 24 24)">
      <path d="M10 21 L30 11 L30 37 L10 28 Z" fill="#fff"/>
      <rect x="5" y="20" width="6" height="9" fill="#fff"/>
      <path d="M13 29 L17 41 L22 40 L19 31"/>
    </g>
    <path d="M33 8 L36 3 M38 12 L44 10 M39 18 L45 19"/>
  </svg>

  <p class="connect">Link in bio or DM to connect</p>
  <div class="handle"><span class="dot"></span><span>velstridebuilders</span></div>

  <p class="website">www.<strong>velstridebuilders</strong>.com</p>
</main>
</body>
</html>
```